MS word document templates for consultancy

I need the following templates for my business using my logo as branding.

- General report template
- Letter head template
- Tender proposal template

The templates should be sleek and with minimal colors, but with a small amount of green and grey where appropriate (as per attached logo and email signature). Font should be consistent with the text in the email signature.

```html
<!DOCTYPE html>
<html lang="en">
<head>
<meta charset="utf-8">
<title>Kindred Ahead Group – Letterhead</title>
<link href="https://fonts.googleapis.com/css2?family=Montserrat:wght@300;400;700&display=swap" rel="stylesheet">
<style>
  :root {
    --brand-green: #2a9447;
    --ink: #141414;
    --paper: #ffffff;
  }
  html, body {
    margin: 0;
    padding: 0;
    overflow: hidden;
    background: var(--paper);
  }
  .letterhead {
    position: relative;
    width: 848px;
    height: 1200px;
    overflow: hidden;
    background: var(--paper);
    font-family: "Montserrat", sans-serif;
  }
  .side-band {
    position: absolute;
    left: 0;
    top: 0;
    width: 43px;
    height: 100%;
    background: var(--brand-green);
  }
  .brand-name {
    position: absolute;
    left: 84px;
    top: 108px;
    width: 354px;
    color: var(--ink);
    font-weight: 400;
    line-height: 1;
  }
  .brand-name__main {
    display: block;
    font-size: 36px;
    letter-spacing: 0.2px;
    white-space: nowrap;
  }
  .brand-name__sub {
    display: block;
    text-align: right;
    font-size: 14px;
    margin-top: 3px;
  }
  .sender-panel {
    position: absolute;
    left: 580px;
    top: 85px;
    right: 0;
    height: 100px;
    background: var(--brand-green);
    color: var(--paper);
    box-sizing: border-box;
    padding: 31px 85px 0 0;
    text-align: right;
  }
  .sender-panel__name {
    font-weight: 700;
    font-size: 14.5px;
    line-height: 1;
  }
  .sender-panel__role {
    font-weight: 300;
    font-size: 14.5px;
    line-height: 1;
    margin-top: 5px;
  }
  .contact-strip {
    position: absolute;
    left: 580px;
    top: 1115px;
    right: 0;
    height: 35px;
    background: var(--brand-green);
    color: var(--paper);
    display: flex;
    align-items: center;
    justify-content: flex-end;
    padding-right: 85px;
    box-sizing: border-box;
    gap: 7px;
    font-weight: 300;
    font-size: 14.5px;
  }
  .contact-strip__icon {
    width: 17px;
    height: 17px;
  }
</style>
</head>
<body>
  <main class="letterhead">
    <div class="side-band"></div>

    <div class="brand-name">
      <span class="brand-name__main">Kindred Ahead</span>
      <span class="brand-name__sub">Group</span>
    </div>

    <section class="sender-panel">
      <div class="sender-panel__name">Sam Rendell</div>
      <div class="sender-panel__role">Managing Director</div>
    </section>

    <footer class="contact-strip">
      <svg class="contact-strip__icon" viewBox="0 0 24 24" fill="none" stroke="currentColor" stroke-width="1.6" aria-hidden="true">
        <circle cx="12" cy="12" r="10.5"/>
        <path d="M8.6 6.8c.4-.3.9-.2 1.1.2l1 1.8c.2.4.1.8-.2 1.1l-.7.6c.6 1.4 1.6 2.5 3 3.1l.6-.7c.3-.3.8-.4 1.1-.2l1.8 1c.4.2.5.8.2 1.1l-.8 1c-.5.5-1.2.7-1.9.5-3-.9-5.3-3.2-6.2-6.2-.2-.7 0-1.4.5-1.9z" fill="currentColor" stroke="none"/>
      </svg>
      <span class="contact-strip__phone">0400 555 019</span>
    </footer>
  </main>
</body>
</html>
```